Liron Vasek Website

Website for my son who is in 7th grade in the US. This will prepare him to show people his accomplishments when applying for a job or going to college. It should have:
* A picture (or multiple pictures)
* A resume page
* A place to share your accomplishments
* Links to his other social profiles
* A contact form

Great to include:
* Internships (show some photos of it along with what you’ve learned).
* Volunteer work.
* A side hustle that you want to highlight

Website sample I like:
https://belinamorud.sitefolio-demo.com/belinamorudtavik

Target Market(s)

For jobs and colleges admissions.

Number of Pages Required

5+ page

Colors

Designer to choose colors to be used in the design.

Requirements
Must have
• * A picture (or multiple pictures)
• * A resume page
• * A place to share your accomplishments
• * Links to his other social profiles
• * A contact form
Nice to have
• Great to include:
• * Internships (show some photos of it along with what you’ve learned).
• * Volunteer work.
• * A side hustle that you want to highlight

```html
<!DOCTYPE html>
<html lang="en">
<head>
<meta charset="utf-8">
<title>Liron Vasek</title>
<link href="https://fonts.googleapis.com/css2?family=Merienda:wght@400;700&family=Nunito:ital,wght@0,400;0,600;0,700;1,700&display=swap" rel="stylesheet">
<style>
:root{
  --teal:#0d5a5f;
  --teal-dark:#0a4a4e;
  --gold:#f1c644;
  --ink:#1b1b1b;
  --text:#555;
  --muted:#777;
  --soft:#efefef;
  --line:#dcdcdc;
  --black:#0b0b0b;
  --white:#fff;
}
*{box-sizing:border-box;margin:0;padding:0}
html,body{width:1200px;height:3836px;overflow:hidden}
body{font-family:'Nunito',sans-serif;color:var(--text);background:var(--white);font-size:14px;line-height:1.6}

/* hero */
.hero{position:relative;height:600px;display:flex}
.hero-panel{width:600px;background:var(--teal);color:var(--white);position:relative}
.brand{position:absolute;left:110px;top:22px;font-family:'Merienda',cursive;font-size:26px;color:var(--gold)}
.nav{position:absolute;left:110px;top:66px;display:flex;gap:18px;font-size:14px;font-weight:600}
.nav a{color:var(--white);text-decoration:none}
.hero-intro{position:absolute;left:110px;top:285px}
.hero-greet{font-family:'Merienda',cursive;color:var(--gold);font-size:26px;font-weight:700}
.hero-name{font-family:'Merienda',cursive;font-size:56px;font-weight:700;line-height:1.2}
.hero-grade{font-size:18px;margin-top:8px}
.hero-photo{flex:1;background:linear-gradient(160deg,#dfe7ec 0%,#b7c8d3 55%,#7d98ab 100%)}
.social-rail{position:absolute;right:14px;top:232px;display:flex;flex-direction:column;gap:2px}
.social-rail span{width:22px;height:34px;background:var(--gold);display:flex;align-items:center;justify-content:center}
.social-rail i{width:8px;height:8px;background:var(--ink);display:block;border-radius:50%}

/* section titles */
.section-title{font-family:'Merienda',cursive;font-style:italic;font-size:46px;color:var(--ink);text-align:center;font-weight:700;line-height:1.35}
.section-title::after{content:"";display:block;width:70px;height:2px;background:var(--ink);margin:10px auto 0}

/* about */
.about{height:508px;padding-top:84px}
.about-copy{width:780px;margin:40px auto 0;text-align:center;font-size:14px;line-height:1.75}
.about-copy p+p{margin-top:10px}
.btn{display:inline-block;background:var(--teal);color:var(--white);font-weight:700;font-size:15px;padding:11px 26px;border-radius:3px;margin-top:26px}
.center{text-align:center}

/* accomplishments */
.accomplish{height:668px;background:var(--soft);padding-top:64px;position:relative}
.timeline{position:relative;width:760px;margin:40px auto 0}
.timeline::before{content:"";position:absolute;left:379px;top:0;bottom:0;width:2px;background:var(--line)}
.tl-row{display:flex;height:150px;position:relative}
.tl-row::after{content:"";position:absolute;left:375px;top:8px;width:10px;height:10px;border-radius:50%;background:var(--teal)}
.tl-side{width:380px;padding:0 30px}
.tl-side.left{text-align:right}
.tl-date{color:var(--teal);font-weight:700;font-size:16px}
.tl-sub{font-weight:700;font-style:italic;color:var(--ink);font-size:15px}
.tl-head{font-family:'Merienda',cursive;font-style:italic;font-weight:700;color:var(--ink);font-size:18px}
.tl-text{font-size:13px;line-height:1.55;margin-top:4px}

/* internships */
.intern{height:576px;background:radial-gradient(circle at 55% 60%,#12686d 0%,var(--teal) 45%,var(--teal-dark) 100%);padding-top:100px;position:relative}
.intern .section-title{color:var(--white)}
.intern .section-title::after{background:var(--white)}
.cards{display:flex;gap:26px;justify-content:center;margin-top:42px}
.card{width:220px;background:var(--white);padding:8px}
.card-photo{height:134px}
.card-title{font-family:'Merienda',cursive;font-style:italic;font-weight:700;color:var(--ink);font-size:16px;margin-top:8px}
.card-text{font-size:12px;line-height:1.45}
.slide-arrow{position:absolute;top:334px;width:22px;height:22px;border-radius:50%;background:var(--white);display:flex;align-items:center;justify-content:center}
.arrow-l{left:-6px}
.arrow-r{right:-6px}

/* volunteer */
.volunteer{height:688px;padding-top:66px}
.vol-cards{display:flex;gap:18px;justify-content:center;margin-top:44px}
.vol-card{width:280px;border:1px solid #e6e6e6}
.vol-photo{height:222px}
.vol-body{padding:14px 12px}
.vol-title{font-family:'Merienda',cursive;font-style:italic;font-weight:700;color:var(--ink);font-size:16px}
.vol-text{font-size:12.5px;line-height:1.55;margin-top:4px}

/* contact + footer */
.contact{position:relative;height:796px}
.contact-ground{position:absolute;left:0;top:30px;width:1200px;height:766px;background:var(--black)}
.contact-wave{position:absolute;left:0;top:0}
.contact-card{position:absolute;left:312px;top:10px;width:648px;height:400px;background:var(--white);padding-top:44px;box-shadow:0 4px 18px rgba(0,0,0,.25)}
.contact-fold{position:absolute;left:-1px;bottom:-22px}
.form-row{display:flex;gap:18px;width:568px;margin:34px auto 0}
.field{flex:1;height:42px;background:#f1f1f1;border-radius:21px;padding:11px 22px;font-size:12px;color:#999}
.field-msg{width:568px;height:104px;margin:16px auto 0;background:#f1f1f1;border-radius:16px;padding:12px 22px;font-size:12px;color:#999}
.submit{display:block;width:186px;margin:24px auto 0;background:var(--teal);color:var(--white);font-weight:700;text-align:center;padding:11px 0;border-radius:22px;font-size:15px;letter-spacing:1px}
.footer-info{position:absolute;left:160px;top:560px;width:880px;display:flex;color:var(--white)}
.info-item{flex:1;display:flex;align-items:center;gap:16px;padding-left:30px;border-left:1px solid #444;font-size:12px;line-height:1.5}
.info-item:first-child{border-left:none}
.info-label{font-size:11px;color:#bbb}
.footer-rule{position:absolute;left:160px;top:640px;width:880px;height:1px;background:#333}
.footer-social{position:absolute;left:0;width:1200px;top:690px;display:flex;justify-content:center;gap:10px}
.footer-social span{width:30px;height:30px;border:1.5px solid var(--white);border-radius:50%}
.copyright{position:absolute;left:0;width:1200px;top:738px;text-align:center;color:var(--white);font-size:12px}
</style>
</head>
<body>

<header class="hero">
  <div class="hero-panel">
    <div class="brand">Liron Vasek</div>
    <nav class="nav"><a>Home</a><a>Portfolio</a><a>Resume</a><a>Achievements</a><a>Blog</a><a>Contact</a></nav>
    <div class="hero-intro">
      <div class="hero-greet">Hey, I'm</div>
      <div class="hero-name">Liron Vasek</div>
      <div class="hero-grade">7th Grade</div>
    </div>
  </div>
  <div class="hero-photo" role="img" aria-label="Portrait photo of Liron Vasek in a light blue shirt"></div>
  <div class="social-rail" aria-label="Social profile links">
    <span><i></i></span><span><i></i></span><span><i></i></span><span><i></i></span>
  </div>
</header>

<section class="about">
  <h2 class="section-title">About Me</h2>
  <div class="about-copy">
    <p>Sed ut perspiciatis unde omnis iste natus error sit voluptatem accusantium doloremque laudantium, totam rem aperiam, eaque ipsa quae ab illo inventore veritatis et quasi architecto beatae vitae dicta sunt explicabo. Nemo enim ipsam voluptatem quia voluptas sit aspernatur aut odit aut fugit.</p>
    <p>At vero eos et accusamus et iusto odio dignissimos ducimus qui blanditiis praesentium voluptatum deleniti atque corrupti quos dolores et quas molestias excepturi sint occaecati cupiditate non provident, similique sunt in culpa qui officia deserunt mollitia animi, id est laborum et dolorum fuga. Et harum quidem rerum facilis est et expedita distinctio. Nam libero tempore, cum soluta nobis est eligendi optio cumque.</p>
  </div>
  <div class="center"><span class="btn">View Full Resume</span></div>
</section>

<section class="accomplish">
  <h2 class="section-title">Accomplishments</h2>
  <div class="timeline">
    <div class="tl-row">
      <div class="tl-side left"><div class="tl-date">2014-2018</div><div class="tl-sub">Lorem ipsum dolor</div></div>
      <div class="tl-side"><div class="tl-head">Sed ut perspiciatis unde</div><p class="tl-text">Nemo enim ipsam voluptatem quia voluptas sit aspernatur aut odit aut fugit, sed quia consequuntur magni dolores eos qui ratione voluptatem sequi nesciunt.</p></div>
    </div>
    <div class="tl-row">
      <div class="tl-side left"><div class="tl-head">Sed ut perspiciatis unde</div><p class="tl-text">Nemo enim ipsam voluptatem quia voluptas sit aspernatur aut odit aut fugit, sed quia consequuntur magni dolores eos qui ratione voluptatem sequi nesciunt.</p></div>
      <div class="tl-side"><div class="tl-date">2014-2018</div><div class="tl-sub">Lorem ipsum dolor</div></div>
    </div>
    <div class="tl-row">
      <div class="tl-side left"><div class="tl-date">2014-2018</div><div class="tl-sub">Lorem ipsum dolor</div></div>
      <div class="tl-side"><div class="tl-head">Sed ut perspiciatis unde</div><p class="tl-text">Nemo enim ipsam voluptatem quia voluptas sit aspernatur aut odit aut fugit, sed quia consequuntur magni dolores eos qui ratione voluptatem sequi nesciunt.</p></div>
    </div>
  </div>
</section>

<section class="intern">
  <h2 class="section-title">Internships</h2>
  <div class="cards">
    <article class="card"><div class="card-photo" role="img" aria-label="Photo of students smiling together at an internship" style="background:linear-gradient(135deg,#7fb5d6,#d9c4a8)"></div><div class="card-title">Lorem ipsum dolor</div><p class="card-text">Sed ut perspiciatis unde omnis iste natus error sit</p></article>
    <article class="card"><div class="card-photo" role="img" aria-label="Photo of a student at an internship workplace" style="background:linear-gradient(135deg,#5d8fb0,#c9a88a)"></div><div class="card-title">Lorem ipsum dolor</div><p class="card-text">Sed ut perspiciatis unde omnis iste natus error sit</p></article>
    <article class="card"><div class="card-photo" role="img" aria-label="Photo of students working together in a classroom" style="background:linear-gradient(135deg,#c8cfc6,#8d9c8a)"></div><div class="card-title">Lorem ipsum dolor</div><p class="card-text">Sed ut perspiciatis unde omnis iste natus error sit</p></article>
    <article class="card"><div class="card-photo" role="img" aria-label="Photo of a team working at computers" style="background:linear-gradient(135deg,#dcdcdc,#9aa8b0)"></div><div class="card-title">Lorem ipsum dolor</div><p class="card-text">Sed ut perspiciatis unde omnis iste natus error sit</p></article>
  </div>
  <span class="slide-arrow arrow-l"><svg width="8" height="10" viewBox="0 0 8 10"><path d="M6 1 2 5l4 4" fill="none" stroke="#333" stroke-width="1.6"/></svg></span>
  <span class="slide-arrow arrow-r"><svg width="8" height="10" viewBox="0 0 8 10"><path d="M2 1l4 4-4 4" fill="none" stroke="#333" stroke-width="1.6"/></svg></span>
</section>

<section class="volunteer">
  <h2 class="section-title">Volunteer Work</h2>
  <div class="vol-cards">
    <article class="vol-card"><div class="vol-photo" role="img" aria-label="Photo of volunteers raising hands against a blue sky" style="background:linear-gradient(180deg,#8ec1ea 0%,#b9d8f0 60%,#6b5a4c 100%)"></div><div class="vol-body"><div class="vol-title">Nemo enim ipsam voluptatem</div><p class="vol-text">Nemo enim ipsam voluptatem quia voluptas sit aspernatur aut odit aut fugit, sed quia consequuntur magni dolores eos qui ratione voluptatem sequi nesciunt.</p></div></article>
    <article class="vol-card"><div class="vol-photo" role="img" aria-label="Photo of a smiling volunteer outdoors" style="background:linear-gradient(160deg,#9fc2d8 0%,#4f6f8c 55%,#c7b59a 100%)"></div><div class="vol-body"><div class="vol-title">Nemo enim ipsam voluptatem</div><p class="vol-text">Nemo enim ipsam voluptatem quia voluptas sit aspernatur aut odit aut fugit, sed quia consequuntur magni dolores eos qui ratione voluptatem sequi nesciunt.</p></div></article>
  </div>
</section>

<section class="contact">
  <div class="contact-ground"></div>
  <svg class="contact-wave" width="1200" height="40" viewBox="0 0 1200 40" aria-hidden="true"><path d="M0 22 Q75 4 150 22 T300 22 T450 22 T600 22 T750 22 T900 22 T1050 22 T1200 22 V40 H0Z" fill="#0b0b0b"/></svg>
  <div class="contact-card">
    <h2 class="section-title">Contact Us</h2>
    <div class="form-row"><div class="field">Name</div><div class="field">Email</div><div class="field">Phone</div></div>
    <div class="field-msg">Message</div>
    <span class="submit">SUBMIT</span>
    <svg class="contact-fold" width="40" height="22" viewBox="0 0 40 22" aria-hidden="true"><path d="M0 0H40L0 22Z" fill="#0d5a5f"/></svg>
  </div>

  <div class="footer-info">
    <div class="info-item">
      <svg width="18" height="30" viewBox="0 0 18 30" aria-hidden="true"><rect x="1" y="1" width="16" height="28" rx="2" fill="none" stroke="#fff" stroke-width="2"/><circle cx="9" cy="24" r="1.6" fill="#fff"/></svg>
      <div><div class="info-label">Call us</div>(555)-014-2290</div>
    </div>
    <div class="info-item">
      <svg width="24" height="30" viewBox="0 0 24 30" aria-hidden="true"><path d="M12 2a8 8 0 0 0-8 8c0 6 8 14 8 14s8-8 8-14a8 8 0 0 0-8-8z" fill="none" stroke="#fff" stroke-width="2"/><circle cx="12" cy="10" r="3" fill="none" stroke="#fff" stroke-width="2"/><ellipse cx="12" cy="27" rx="10" ry="2.4" fill="none" stroke="#fff" stroke-width="1.5"/></svg>
      <div><div class="info-label">Addres</div>#10, Duis aute irure dolor in<br>reprehenderit in voluptate</div>
    </div>
    <div class="info-item">
      <svg width="30" height="22" viewBox="0 0 30 22" aria-hidden="true"><rect x="1" y="1" width="28" height="20" rx="1" fill="none" stroke="#fff" stroke-width="2"/><path d="M1 1l14 11L29 1" fill="none" stroke="#fff" stroke-width="2"/></svg>
      <div><div class="info-label">Email</div>info@lironvasek.com</div>
    </div>
  </div>
  <div class="footer-rule"></div>
  <div class="footer-social" aria-label="Social profile links"><span></span><span></span><span></span><span></span></div>
  <div class="copyright">© Copyrights 2019 | All Rights Reserved</div>
</section>

</body>
</html>
```